Lumo in Spain

web design of search platform. Enclosed please find an excel sheet with the info, as well as a picture of a webdesign we like (boxwander). Idea is to have a modern, inviting website with main colors white, red and dark grey (text). The logo (mork in spain) will be changed to lumo, but you can use this logo for now. Please also use the character enclosed. We can ask this designer to also design the pictograms for the other items, just use something from the net for the design and we'll have it changed afterwards. The texts are enclosed in the word doc enclosed. Thank you!

Target Market(s)

people looking for property in Spain

Industry/Entity Type

Real Estate

Number of Pages Required

1 page

Other font styles liked:
• a font that goes well with the logo

Colors
ec1f27

Requirements
Must have
• a lot of white
• clean but fun look

```html
<!DOCTYPE html>
<html lang="en">
<head>
<meta charset="utf-8">
<title>Lumo in Spain – web design</title>
<link href="https://fonts.googleapis.com/css2?family=Open+Sans:wght@400;600;700&display=swap" rel="stylesheet">
<style>
:root{
  --red:#ec1f27;
  --ink:#3a3a3a;
  --muted:#8a8a8a;
  --line:#d8d8d8;
  --board:#edeced;
  --soft:#f6f6f6;
  --white:#ffffff;
}
*{box-sizing:border-box;margin:0;padding:0}
html,body{width:1028px;height:1200px;overflow:hidden;background:var(--board);font-family:"Open Sans",Arial,sans-serif;color:var(--ink)}
h1,h2,h3,h4,h5{font-weight:400}
.stage{position:absolute;left:0;top:0;width:1774px;height:2072px;transform:scale(.5795);transform-origin:0 0;background:var(--board)}
.page{position:absolute;width:403px;background:var(--white);overflow:hidden;box-shadow:0 0 3px rgba(0,0,0,.08)}
.page > *{position:absolute}
.ctr{left:0;width:100%;text-align:center}
.brand{left:37px;top:22px;font-size:12px;font-weight:400;color:var(--ink);white-space:nowrap;line-height:1}
.burger{right:37px;top:20px;width:16px;height:11px;border-top:1px solid var(--ink);border-bottom:1px solid var(--ink)}
.burger::after{content:"";position:absolute;left:0;right:0;top:4px;border-top:1px solid var(--ink)}
.hero-title{left:37px;top:92px;font-size:11.5px;font-weight:400;white-space:nowrap;z-index:2}
.hero-title em{font-style:normal;color:var(--red);font-weight:600}
.hero-search{left:37px;top:113px;width:164px;height:18px;border:1px solid var(--line);background:var(--white);font-size:4px;padding:6px 0 0 12px;color:var(--muted);z-index:2}
.pin{position:absolute;left:5px;top:5px;width:4px;height:6px;border:1px solid var(--ink);border-radius:50% 50% 50% 50%/60% 60% 40% 40%}
.btn{background:var(--red);color:var(--white);font-size:5px;font-weight:700;border-radius:9px;text-align:center;line-height:18px;height:18px}
.hero-btn{left:37px;top:139px;width:70px;z-index:2}
.mascot{left:228px;top:64px;width:170px;height:140px;z-index:1;border-radius:45% 45% 40% 40%;background:radial-gradient(circle at 50% 40%,#9a9a9a 0,#5d5d5d 45%,rgba(255,255,255,0) 70%)}
.sec-title{font-size:10.5px;color:var(--red);font-weight:400}
.para{font-size:4.6px;line-height:10px;color:var(--muted);text-align:center}
.steps{left:15px;width:373px;height:73px;border:1px dashed #c4c4c4;border-radius:40px}
.step{width:110px;text-align:center}
.step svg{display:block;margin:0 auto 8px}
.step h4{font-size:6px;font-weight:400;margin-bottom:5px}
.step h4.on{color:var(--red)}
.step p{font-size:4px;line-height:8px;color:var(--muted)}
.vline{left:201px;width:1px;height:41px;background:var(--red)}
.sub{font-size:6px;color:var(--ink)}
.sheet{background:linear-gradient(90deg,#3c3f44 0 30%,#f4f4f4 30% 100%);border:1px solid #ddd;box-shadow:0 3px 6px rgba(0,0,0,.12)}
.sheet.side{opacity:.55}
.dots{left:191px;width:22px;height:9px}
.dots i{position:absolute;top:0;width:9px;height:9px;border-radius:50%;background:var(--red)}
.dots i+i{left:12px;background:#9a9a9a}
.band{left:0;width:403px;background:var(--red)}
.band-title{font-size:10px;font-weight:400;color:var(--white)}
.card{width:159px;height:40px;background:var(--white);border-radius:3px;padding:5px 5px 0 48px}
.card svg{position:absolute;left:10px;top:8px}
.card h5{font-size:6px;color:var(--red);font-weight:400;margin-bottom:2px}
.card p{font-size:3.4px;line-height:5.5px;color:var(--muted)}
.btn-w{background:var(--white);color:var(--red);font-size:5px;font-weight:700;border-radius:9px;text-align:center;height:18px;line-height:18px;width:64px;left:169px}
.photo{height:55px;width:77px}
.ph-a{background:linear-gradient(#bcd6ee 0 45%,#e8ddc9 45% 70%,#6d9a45 70%)}
.ph-b{background:linear-gradient(#9cc2e8 0 40%,#c98a5a 40% 72%,#b9a888 72%)}
.ph-c{background:linear-gradient(#8fb6e0 0 38%,#d9cbb5 38% 75%,#7ea85a 75%)}
.ph-d{background:linear-gradient(#dfe9f2 0 30%,#5a6b4a 30% 70%,#5f8f3c 70%)}
.ph-n1{background:linear-gradient(#1f3d6e 0 45%,#c9a57a 45% 75%,#2c3a55 75%)}
.ph-n2{background:linear-gradient(#6fa2d9 0 40%,#d5d7da 40% 80%,#9aa3ad 80%)}
.ph-n3{background:linear-gradient(#24497e 0 40%,#e0b46f 40% 70%,#3e8fb8 70%)}
.ph-n4{background:linear-gradient(#4f86c8 0 35%,#e8c07a 35% 72%,#2f9bc9 72%)}
.ph-n5{background:linear-gradient(#5e96d4 0 40%,#e4d3b6 40% 72%,#6bb7d6 72%)}
.ph-n6{background:linear-gradient(#2d3d55 0 40%,#c8c9cc 40% 80%,#4a4e55 80%)}
.arrow{width:12px;height:12px;border:1px solid var(--red);border-radius:50%}
.arrow::after{content:"";position:absolute;left:4px;top:3.5px;width:3px;height:3px;border-left:1px solid var(--red);border-bottom:1px solid var(--red);transform:rotate(45deg)}
.arrow.next::after{left:3px;transform:rotate(-135deg)}
.cta{left:0;width:403px;height:92px;background:var(--soft)}
.cta-in{left:83px;width:238px;height:18px;border:1px solid var(--line);background:var(--white);font-size:4px;padding:6px 0 0 12px;color:var(--muted)}
.cta-in .btn{position:absolute;right:-1px;top:-1px;width:71px}
.foot{font-size:4px;color:var(--muted);left:125px;white-space:nowrap}
.social{width:40px;height:11px}
.social i{position:absolute;top:0;width:11px;height:11px;border:1px solid var(--red);border-radius:50%}
.tl-circle{left:180px;width:44px;height:44px;border:1.5px solid var(--red);border-radius:50%}
.tl-circle svg{position:absolute;left:11px;top:11px}
.tl{width:135px}
.tl h5{font-size:5.2px;color:var(--red);font-weight:600;margin-bottom:4px}
.tl p{font-size:3.6px;line-height:7px;color:var(--muted)}
.faq{left:62px;width:280px;height:26px;border:1px solid var(--line);background:var(--white);font-size:5.5px;line-height:24px;padding-left:25px}
.faq svg{position:absolute;left:7px;top:7px}
.faq::after{content:"";position:absolute;right:9px;top:8px;width:4px;height:4px;border-right:1px solid var(--ink);border-bottom:1px solid var(--ink);transform:rotate(45deg)}
.filter{width:52px;height:14px;border:1px solid #e2e2e2;font-size:3.6px;color:var(--muted);padding:4px 0 0 4px}
.filter::after{content:"";position:absolute;right:4px;top:5px;border:1.5px solid transparent;border-top-color:#888}
.cap{font-size:4px;color:var(--ink)}
.cap span{color:var(--muted)}
.pager{left:155px;top:530px;font-size:5px;display:flex;gap:9px;align-items:center}
.pager .cur{background:var(--red);color:var(--white);padding:1px 3px}
</style>
</head>
<body>
<div class="stage">

<!-- ============ PAGE ONE ============ -->
<section class="page" style="left:159px;top:169px;height:1211px">
  <p class="brand">mork in spain</p>
  <div class="burger"></div>
  <h1 class="hero-title">estate agents compete, <em>you win</em></h1>
  <div class="hero-search"><i class="pin"></i>Enter the city or area where you want to buy or sell</div>
  <div class="btn hero-btn">COMPARE AGENTS</div>
  <div class="mascot" role="img" aria-label="Lumo mascot character with magnifying glass giving a thumbs up"></div>

  <h2 class="sec-title ctr" style="top:233px">how lumo's free service works</h2>
  <p class="para" style="left:95px;top:252px;width:213px">Stay anonymous while the estate agents of your choice compete for you by sending you their best proposal, thus guaranteeing you the best deal possible. With lumo you will find the best real estate agent for you!</p>
  <div class="steps" style="top:314px"></div>
  <div class="step" style="left:35px;top:303px"><svg width="20" height="18" viewBox="0 0 20 18"><rect x="1" y="4" width="13" height="13" fill="none" stroke="#888" stroke-width="1.2"/><path d="M7 12l10-10 2 2-10 10-3 1z" fill="none" stroke="#888" stroke-width="1.2"/></svg><h4>1. Enter your preferences</h4><p>Answer a few short questions and, within seconds and at no cost or obligation to you, lumo will filter the best agents for you.</p></div>
  <div class="step" style="left:147px;top:303px"><svg width="22" height="18" viewBox="0 0 22 18"><path d="M2 6h17M15 2l4 4-4 4M20 12H3M7 8l-4 4 4 4" fill="none" stroke="#ec1f27" stroke-width="2"/></svg><h4 class="on">2. Compare proposals</h4><p>Choose up to 5 agents you want to compete for you. Within 24 hours you will receive their best proposal.</p></div>
  <div class="step" style="left:259px;top:303px"><svg width="18" height="18" viewBox="0 0 18 18"><circle cx="9" cy="5" r="4" fill="#999"/><path d="M1 18c0-6 16-6 16 0z" fill="#999"/></svg><h4>3. Select your agent</h4><p>At no obligation, select the proposal you like best. Only this winning agent will contact you to help you find or sell your property.</p></div>

  <div class="vline" style="top:428px"></div>
  <h2 class="sec-title ctr" style="top:483px">compare proposals before selecting an agent</h2>
  <p class="sub ctr" style="top:501px">view sample proposal</p>
  <div class="sheet side" style="left:37px;top:554px;width:91px;height:59px" role="img" aria-label="sample agent proposal sheet"></div>
  <div class="sheet side" style="left:277px;top:554px;width:91px;height:59px" role="img" aria-label="sample agent proposal sheet"></div>
  <div class="sheet" style="left:138px;top:528px;width:128px;height:84px" role="img" aria-label="sample agent proposal sheet with profile and achievements"></div>
  <div class="dots" style="top:648px"><i></i><i></i></div>

  <div class="band" style="top:696px;height:189px"></div>
  <h2 class="band-title ctr" style="top:724px">lumo: the smartest way to find the best real estate agent for you</h2>
  <div class="card" style="left:37px;top:756px"><svg width="30" height="20" viewBox="0 0 30 20"><circle cx="15" cy="5" r="4" fill="#ec1f27"/><circle cx="6" cy="8" r="3" fill="#ec1f27"/><circle cx="24" cy="8" r="3" fill="#ec1f27"/><path d="M8 20c0-8 14-8 14 0zM0 20c0-6 10-6 10 0zM20 20c0-6 10-6 10 0z" fill="#ec1f27"/></svg><h5>simplify your search</h5><p>lumo simplifies the process of finding the best estate agent for you, based on your needs.</p></div>
  <div class="card" style="left:207px;top:756px"><svg width="22" height="22" viewBox="0 0 22 22"><rect x="1" y="10" width="5" height="11" fill="#ec1f27"/><path d="M8 10l5-9c3 0 3 3 2 6h6c1 0 1 2 0 3l-2 10H8z" fill="#ec1f27"/></svg><h5>get the best deal</h5><p>by comparing proposals personalized just for you, you'll be able to find out if you're getting the best agent and the best deal.</p></div>
  <div class="card" style="left:37px;top:808px"><svg width="22" height="22" viewBox="0 0 22 22"><circle cx="11" cy="11" r="10" fill="#ec1f27"/><circle cx="7.5" cy="9" r="2" fill="#fff"/><circle cx="14.5" cy="9" r="2" fill="#fff"/><path d="M6 14q5 4 10 0" stroke="#fff" fill="none" stroke-width="1.5"/></svg><h5>anonymity</h5><p>lumo guarantees you anonymity and no annoying sales calls or mails. Your personal information will only be shared with the agent of your choice.</p></div>
  <div class="card" style="left:207px;top:808px"><svg width="22" height="22" viewBox="0 0 22 22"><polygon points="11,0 14,4 19,3 18,8 22,11 18,14 19,19 14,18 11,22 8,18 3,19 4,14 0,11 4,8 3,3 8,4" fill="#ec1f27"/><text x="11" y="13" font-size="5" fill="#fff" text-anchor="middle" font-family="Open Sans,sans-serif">FREE</text></svg><h5>100% free</h5><p>lumo's service is 100% free of charge for you, with no obligations. Agents don't pay to be listed, so you get the best match.</p></div>

  <h2 class="sec-title ctr" style="top:920px">featured properties for sale</h2>
  <p class="para" style="left:60px;top:942px;width:283px">In Spain, every agent has access to the same properties for sale. Therefore, the most important first step is to find the real estate agent who is willing to do the most for you. The agent of your choice will show you the best properties for sale in your area and guide you through the entire process.</p>
  <div class="arrow" style="left:12px;top:1009px"></div>
  <div class="photo ph-a" style="left:37px;top:988px" role="img" aria-label="white villa with lawn"></div>
  <div class="photo ph-b" style="left:121px;top:988px" role="img" aria-label="terracotta roof house"></div>
  <div class="photo ph-c" style="left:205px;top:988px" role="img" aria-label="two-storey family house"></div>
  <div class="photo ph-d" style="left:288px;top:988px" role="img" aria-label="house among trees and flowers"></div>
  <div class="arrow next" style="left:378px;top:1009px"></div>

  <div class="cta" style="top:1077px"></div>
  <h2 class="sec-title ctr" style="top:1099px">compare real estate agents and save thousands</h2>
  <div class="cta-in" style="top:1124px"><i class="pin"></i>Enter the city or area where you want to buy or sell<div class="btn">COMPARE AGENTS</div></div>
  <p class="foot" style="top:1191px">Sitemap &nbsp; | &nbsp; Privacy Policy &nbsp; | &nbsp; Copyright © 2019 All Rights Reserved.</p>
  <div class="social" style="left:324px;top:1188px"><i style="left:0"></i><i style="left:15px"></i><i style="left:30px"></i></div>
</section>

<!-- ============ PAGE TWO ============ -->
<section class="page" style="left:681px;top:169px;height:1734px">
  <p class="brand">mork in spain</p>
  <div class="burger"></div>
  <h1 class="hero-title">estate agents compete, <em>you win</em></h1>
  <div class="hero-search"><i class="pin"></i>Enter the city or area where you want to buy or sell</div>
  <div class="btn hero-btn">COMPARE AGENTS</div>
  <div class="mascot" role="img" aria-label="Lumo mascot character with magnifying glass giving a thumbs up"></div>

  <h2 class="sec-title ctr" style="top:233px">how lumo's free service works</h2>
  <div class="tl-circle" style="top:270px"><svg width="20" height="20" viewBox="0 0 20 20"><circle cx="8" cy="8" r="6" fill="none" stroke="#555" stroke-width="1.3"/><path d="M12.5 12.5l6 6" stroke="#555" stroke-width="1.6"/></svg></div>
  <div class="tl" style="left:237px;top:276px"><h5>tell lumo what you are looking for</h5><p>Answer a few short questions about your goals and preferences, and lumo will start filtering agents to find the best ones for you.</p></div>
  <div class="tl" style="left:38px;top:345px"><h5>review your top agent matches</h5><p>In a matter of seconds, we'll present you with up to 5 top agent matches based on your needs. Our results are 100% free, data-driven and unbiased. Take a look at each agent's profile and select the agents you want to compete for you.</p></div>
  <div class="tl-circle" style="top:342px"><svg width="20" height="20" viewBox="0 0 20 20"><polygon points="10,1 12.6,7 19,7.4 14,11.5 15.6,18 10,14.5 4.4,18 6,11.5 1,7.4 7.4,7" fill="none" stroke="#555" stroke-width="1.2"/></svg></div>
  <div class="tl-circle" style="top:411px"><svg width="20" height="20" viewBox="0 0 20 20"><circle cx="10" cy="10" r="8" fill="none" stroke="#555" stroke-width="1.2"/><circle cx="10" cy="10" r="4" fill="none" stroke="#555" stroke-width="1.2"/></svg></div>
  <div class="tl" style="left:237px;top:414px"><h5>receive proposals within 24 hours</h5><p>Compare the different proposals for total savings, services and agent background information from top estate agents in your area. You're about to make one of the largest financial decisions of your life - lumo helps you make a fully informed decision.</p></div>
  <div class="tl" style="left:38px;top:487px"><h5>select your agent</h5><p>At no cost and no obligation for you, select the agent you feel best suits your needs. No personal information is shared with real estate agents until you have accepted the winning bid.</p></div>
  <div class="tl-circle" style="top:483px"><svg width="20" height="20" viewBox="0 0 20 20"><path d="M7 18V6a1.5 1.5 0 013 0v5l6 1v6z" fill="none" stroke="#555" stroke-width="1.2"/></svg></div>
  <div class="tl-circle" style="top:554px"><svg width="20" height="20" viewBox="0 0 20 20"><circle cx="10" cy="6" r="4" fill="none" stroke="#555" stroke-width="1.2"/><path d="M3 19c0-7 14-7 14 0z" fill="none" stroke="#555" stroke-width="1.2"/></svg></div>
  <div class="tl" style="left:237px;top:561px"><h5>agent contact</h5><p>The agent of your choice will contact you and, if you hire him, guide you through the entire buying, selling or renting process.</p></div>
  <div class="tl" style="left:38px;top:629px"><h5>close the deal on your house!</h5><p>Your top agent closes the deal for you at the best price possible. Your estate agent just saved you lots of time and money.</p></div>
  <div class="tl-circle" style="top:626px"><svg width="20" height="20" viewBox="0 0 20 20"><path d="M2 10L10 2l8 8M4 8v10h12V8M8 18v-5h4v5" fill="none" stroke="#555" stroke-width="1.2"/></svg></div>

  <div class="band" style="top:716px;height:226px"></div>
  <h2 class="band-title ctr" style="top:744px">why thousands use lumo to find an agent</h2>
  <div class="card" style="left:38px;top:776px"><svg width="22" height="22" viewBox="0 0 22 22"><circle cx="9" cy="9" r="7" fill="none" stroke="#ec1f27" stroke-width="1.5"/><path d="M14 14l7 7" stroke="#ec1f27" stroke-width="2"/></svg><h5>Easy to use</h5><p>Sign up and get started in just a few easy steps. No more calling around, you'll receive up to 5 proposals from top real estate agents.</p></div>
  <div class="card" style="left:208px;top:776px"><svg width="24" height="20" viewBox="0 0 24 20"><path d="M1 6l6-3 5 3 5-3 6 3v7l-6 4-5-3-5 3-6-4z" fill="none" stroke="#ec1f27" stroke-width="1.3"/></svg><h5>Get the best deal</h5><p>Sit back while agents compete by offering you their best commission rates and services they will perform if they win your listing.</p></div>
  <div class="card" style="left:38px;top:828px"><svg width="22" height="22" viewBox="0 0 22 22"><circle cx="11" cy="11" r="5" fill="none" stroke="#ec1f27" stroke-width="1.5"/><path d="M11 1v4M11 17v4M1 11h4M17 11h4M4 4l3 3M15 15l3 3M18 4l-3 3M4 18l3-3" stroke="#ec1f27" stroke-width="1.3"/></svg><h5>You're in control</h5><p>There is no obligation when selecting an agent. If for any reason you do not feel satisfied with your selection, you will have the option of selecting another agent from the offers received.</p></div>
  <div class="card" style="left:208px;top:828px"><svg width="22" height="22" viewBox="0 0 22 22"><circle cx="11" cy="11" r="9" fill="none" stroke="#ec1f27" stroke-width="1.5"/><path d="M4 18L18 4" stroke="#ec1f27" stroke-width="1.5"/></svg><h5>No 'stalking' by agents</h5><p>You remain anonymous until such time as you select the agent that best meets your needs for services and cost savings. Only the agent you select receives your contact information.</p></div>
  <div class="btn-w" style="top:891px">GET STARTED</div>

  <div style="left:0;top:942px;width:403px;height:180px;background:var(--soft)"></div>
  <h2 class="sec-title ctr" style="top:980px">still have questions about how lumo works?</h2>
  <p class="para" style="left:0;width:403px;top:1002px">Here are just a few things people frequently ask about lumo. Check more at <span style="color:var(--red)">FAQs</span>.</p>
  <div class="faq" style="top:1024px"><svg width="11" height="11" viewBox="0 0 11 11"><circle cx="4.5" cy="4.5" r="3.5" fill="none" stroke="#ec1f27"/><path d="M7 7l3.5 3.5" stroke="#ec1f27"/></svg>Is lumo a free service?</div>
  <div class="faq" style="top:1055px"><svg width="11" height="11" viewBox="0 0 11 11"><circle cx="4.5" cy="4.5" r="3.5" fill="none" stroke="#ec1f27"/><path d="M7 7l3.5 3.5" stroke="#ec1f27"/></svg>Will my information stay anonymous?</div>
  <div class="faq" style="top:1085px"><svg width="11" height="11" viewBox="0 0 11 11"><circle cx="4.5" cy="4.5" r="3.5" fill="none" stroke="#ec1f27"/><path d="M7 7l3.5 3.5" stroke="#ec1f27"/></svg>What is a proposal and what does it include?</div>

  <div class="vline" style="top:1143px"></div>
  <h2 class="sec-title ctr" style="top:1196px">compare proposals before selecting an agent</h2>
  <p class="sub ctr" style="top:1214px">view sample proposal</p>
  <div class="sheet side" style="left:37px;top:1266px;width:91px;height:59px" role="img" aria-label="sample agent proposal sheet"></div>
  <div class="sheet side" style="left:277px;top:1266px;width:91px;height:59px" role="img" aria-label="sample agent proposal sheet"></div>
  <div class="sheet" style="left:138px;top:1240px;width:128px;height:84px" role="img" aria-label="sample agent proposal sheet with profile and achievements"></div>
  <div class="dots" style="top:1360px"><i></i><i></i></div>

  <h2 class="sec-title ctr" style="top:1440px">featured properties for sale</h2>
  <p class="para" style="left:60px;top:1462px;width:283px">In Spain, every agent has access to the same properties for sale. Therefore, the most important first step is to find the real estate agent who is willing to do the most for you. The agent of your choice will show you the best properties for sale in your area and guide you through the entire process.</p>
  <div class="arrow" style="left:12px;top:1529px"></div>
  <div class="photo ph-a" style="left:37px;top:1508px" role="img" aria-label="white villa with lawn"></div>
  <div class="photo ph-b" style="left:121px;top:1508px" role="img" aria-label="terracotta roof house"></div>
  <div class="photo ph-c" style="left:205px;top:1508px" role="img" aria-label="two-storey family house"></div>
  <div class="photo ph-d" style="left:288px;top:1508px" role="img" aria-label="house among trees and flowers"></div>
  <div class="arrow next" style="left:378px;top:1529px"></div>

  <div class="cta" style="top:1596px"></div>
  <h2 class="sec-title ctr" style="top:1618px">compare real estate agents and save thousands</h2>
  <div class="cta-in" style="top:1644px"><i class="pin"></i>Enter the city or area where you want to buy or sell<div class="btn">COMPARE AGENTS</div></div>
  <p class="foot" style="top:1711px">Sitemap &nbsp; | &nbsp; Privacy Policy &nbsp; | &nbsp; Copyright © 2019 All Rights Reserved.</p>
  <div class="social" style="left:324px;top:1708px"><i style="left:0"></i><i style="left:15px"></i><i style="left:30px"></i></div>
</section>

<!-- ============ PAGE THREE ============ -->
<section class="page" style="left:1212px;top:169px;height:1588px">
  <p class="brand">mork in spain</p>
  <div class="burger"></div>
  <h1 class="hero-title">your dream home at the <em>best price</em></h1>
  <div class="hero-search"><i class="pin"></i>Enter the city or area where you want to buy or sell</div>
  <div class="btn hero-btn">COMPARE AGENTS</div>
  <div class="mascot" role="img" aria-label="Lumo mascot character with magnifying glass giving a thumbs up"></div>

  <h2 class="sec-title ctr" style="top:233px">newly build properties for sale in Spain</h2>
  <p class="para" style="left:58px;top:256px;width:287px">In Spain, every agent has access to the same properties for sale. Therefore, the most important first step is to find the real estate agent who is willing to do the most for you. The agent of your choice will show you the best properties for sale in your area and guide you through the entire process.</p>
  <div class="filter" style="left:37px;top:305px">All Actions</div>
  <div class="filter" style="left:93px;top:305px">All Types</div>
  <div class="filter" style="left:149px;top:305px">All Counties</div>
  <div class="filter" style="left:205px;top:305px">All Cities</div>
  <div class="filter" style="left:261px;top:305px">All Areas</div>
  <div class="filter" style="left:317px;top:305px">Default</div>
  <div class="photo ph-n1" style="left:37px;top:341px;width:105px;height:61px" role="img" aria-label="mansion lit at dusk"></div>
  <div class="photo ph-n2" style="left:149px;top:341px;width:105px;height:61px" role="img" aria-label="modern white mansion"></div>
  <div class="photo ph-n3" style="left:261px;top:341px;width:105px;height:61px" role="img" aria-label="villa with pool at night"></div>
  <p class="cap" style="left:37px;top:410px">Mansion in Barcelona <span>by Agentio</span></p>
  <p class="cap" style="left:149px;top:410px">Mansion in Barcelona <span>by Agentio</span></p>
  <p class="cap" style="left:261px;top:410px">Mansion in Barcelona <span>by Agentio</span></p>
  <div class="photo ph-n4" style="left:37px;top:431px;width:105px;height:61px" role="img" aria-label="villa with pool"></div>
  <div class="photo ph-n5" style="left:149px;top:431px;width:105px;height:61px" role="img" aria-label="modern villa with pool"></div>
  <div class="photo ph-n6" style="left:261px;top:431px;width:105px;height:61px" role="img" aria-label="grey stone mansion"></div>
  <p class="cap" style="left:37px;top:499px">Mansion in Barcelona <span>by Agentio</span></p>
  <p class="cap" style="left:149px;top:499px">Mansion in Barcelona <span>by Agentio</span></p>
  <p class="cap" style="left:261px;top:499px">Mansion in Barcelona <span>by Agentio</span></p>
  <div class="pager"><span>‹</span><span class="cur">1</span><span>2</span><span>3</span><span>4</span><span>5</span><span>›</span></div>

  <div style="left:0;top:578px;width:403px;height:139px;background:var(--soft)"></div>
  <h2 class="sec-title ctr" style="top:604px">featured properties for sale</h2>
  <div class="arrow" style="left:12px;top:655px"></div>
  <div class="photo ph-a" style="left:37px;top:634px;height:54px;width:78px" role="img" aria-label="white villa with lawn"></div>
  <div class="photo ph-b" style="left:120px;top:634px;height:54px;width:78px" role="img" aria-label="terracotta roof house"></div>
  <div class="photo ph-c" style="left:204px;top:634px;height:54px;width:78px" role="img" aria-label="two-storey family house"></div>
  <div class="photo ph-d" style="left:288px;top:634px;height:54px;width:78px" role="img" aria-label="house among trees and flowers"></div>
  <div class="arrow next" style="left:378px;top:655px"></div>

  <div class="band" style="top:728px;height:227px"></div>
  <h2 class="band-title ctr" style="top:756px">lumo: the smartest way to find the best real estate agent for you</h2>
  <div class="card" style="left:37px;top:788px"><svg width="22" height="22" viewBox="0 0 22 22"><circle cx="9" cy="9" r="7" fill="none" stroke="#ec1f27" stroke-width="1.5"/><path d="M14 14l7 7" stroke="#ec1f27" stroke-width="2"/></svg><h5>Easy to use</h5><p>Sign up and get started in just a few easy steps. No more calling around, you'll receive up to 5 proposals from top real estate agents.</p></div>
  <div class="card" style="left:207px;top:788px"><svg width="24" height="20" viewBox="0 0 24 20"><path d="M1 6l6-3 5 3 5-3 6 3v7l-6 4-5-3-5 3-6-4z" fill="none" stroke="#ec1f27" stroke-width="1.3"/></svg><h5>Get the best deal</h5><p>Sit back while agents compete by offering you their best commission rates and services they will perform if they win your listing.</p></div>
  <div class="card" style="left:37px;top:839px"><svg width="22" height="22" viewBox="0 0 22 22"><circle cx="11" cy="11" r="5" fill="none" stroke="#ec1f27" stroke-width="1.5"/><path d="M11 1v4M11 17v4M1 11h4M17 11h4M4 4l3 3M15 15l3 3M18 4l-3 3M4 18l3-3" stroke="#ec1f27" stroke-width="1.3"/></svg><h5>You're in control</h5><p>There is no obligation when selecting an agent. If for any reason you do not feel satisfied with your selection, you will have the option of selecting another agent from the offers received.</p></div>
  <div class="card" style="left:207px;top:839px"><svg width="22" height="22" viewBox="0 0 22 22"><circle cx="11" cy="11" r="9" fill="none" stroke="#ec1f27" stroke-width="1.5"/><path d="M4 18L18 4" stroke="#ec1f27" stroke-width="1.5"/></svg><h5>No 'stalking' by agents</h5><p>You remain anonymous until such time as you select the agent that best meets your needs for services and cost savings. Only the agent you select receives your contact information.</p></div>
  <div class="btn-w" style="top:902px">GET STARTED</div>

  <h2 class="sec-title ctr" style="top:990px">how lumo's free service works</h2>
  <p class="para" style="left:95px;top:1009px;width:213px">Stay anonymous while the estate agents of your choice compete for you by sending you their best proposal, thus guaranteeing you the best deal possible. With lumo you will find the best real estate agent for you!</p>
  <div class="steps" style="top:1069px"></div>
  <div class="step" style="left:35px;top:1059px"><svg width="20" height="18" viewBox="0 0 20 18"><rect x="1" y="4" width="13" height="13" fill="none" stroke="#888" stroke-width="1.2"/><path d="M7 12l10-10 2 2-10 10-3 1z" fill="none" stroke="#888" stroke-width="1.2"/></svg><h4>1. Enter your preferences</h4><p>Answer a few short questions and, within seconds and at no cost or obligation to you, lumo will filter the best agents for you.</p></div>
  <div class="step" style="left:147px;top:1059px"><svg width="22" height="18" viewBox="0 0 22 18"><path d="M2 6h17M15 2l4 4-4 4M20 12H3M7 8l-4 4 4 4" fill="none" stroke="#ec1f27" stroke-width="2"/></svg><h4 class="on">2. Compare proposals</h4><p>Choose up to 5 agents you want to compete for you. Within 24 hours you will receive their best proposal.</p></div>
  <div class="step" style="left:259px;top:1059px"><svg width="18" height="18" viewBox="0 0 18 18"><circle cx="9" cy="5" r="4" fill="#999"/><path d="M1 18c0-6 16-6 16 0z" fill="#999"/></svg><h4>3. Select your agent</h4><p>At no obligation, select the proposal you like best. Only this winning agent will contact you to help you find or sell your property.</p></div>

  <div class="vline" style="top:1184px"></div>
  <h2 class="sec-title ctr" style="top:1240px">compare proposals before selecting an agent</h2>
  <p class="sub ctr" style="top:1258px">view sample proposal</p>
  <div class="sheet side" style="left:37px;top:1310px;width:91px;height:59px" role="img" aria-label="sample agent proposal sheet"></div>
  <div class="sheet side" style="left:277px;top:1310px;width:91px;height:59px" role="img" aria-label="sample agent proposal sheet"></div>
  <div class="sheet" style="left:138px;top:1284px;width:128px;height:84px" role="img" aria-label="sample agent proposal sheet with profile and achievements"></div>
  <div class="dots" style="top:1404px"><i></i><i></i></div>

  <div class="cta" style="top:1451px"></div>
  <h2 class="sec-title ctr" style="top:1473px">compare real estate agents and save thousands</h2>
  <div class="cta-in" style="top:1499px"><i class="pin"></i>Enter the city or area where you want to buy or sell<div class="btn">COMPARE AGENTS</div></div>
  <p class="foot" style="top:1566px">Sitemap &nbsp; | &nbsp; Privacy Policy &nbsp; | &nbsp; Copyright © 2019 All Rights Reserved.</p>
  <div class="social" style="left:324px;top:1563px"><i style="left:0"></i><i style="left:15px"></i><i style="left:30px"></i></div>
</section>

</div>
</body>
</html>
```